Car rental website design for a UAE car rental company

This project is about creating a new website design for a car rental company located in Dubai (United Arab Emirates), I opened the same project a few months ago but I didn't receive a lot of appealing entries so I closed it but this time I am marking the project as guaranteed to avoid such situation again, if you have already provided a design before then please re-submit again on this project so that it is considered while reviewing all the designs

A few important things:

1- We need a simple non-complex design
2- The final deliverable would be 2 screens (PSD, JPEG ... etc), the first screen is for the home page and the second screen is for an internal page
3- The home page must have a section that end users can use to rent a car online directly from the home page instead of going into some inner pages
4- The current website is very old and not very appealing so avoid creating a similar design (www.crestvane-autos.example)
5- The name is Crestvane but the company rents normal cars (no Limousin cars will be rented) so avoid adding any fancy cars in the images/graphics used in the design, just normal end users cars
6- The expected pages would be: home, About us, Our team, Strategy, Contact us and links to social media pages
7- The attachments include the company's logo and some screens from other car rental companies that provide online rentals/payments

If you have any questions please feel free to ask and please note that we will need the designs urgently

Thanks

Target Market(s)

Dubai - United Arab Emirates

Industry/Entity Type

It Company

Number of Pages Required

2 page

Font styles to use
Sans Serif

Requirements
Must have
• Check the project details
Nice to have
Should not have

```html
<!DOCTYPE html>
<html lang="en">
<head>
<meta charset="utf-8">
<title>Crestvane Rent A Car</title>
<link rel="stylesheet" href="https://fonts.googleapis.com/css2?family=Bitter:wght@400;500&family=Open+Sans:wght@400;600&display=swap">
<style>
:root{
  --maroon:#a3093d;
  --grey:#8a8a8a;
  --text:#333;
  --line:#c9c9c9;
  --hero:#d6d5da;
  --band:#f4f4f4;
  --white:#fff;
}
*{box-sizing:border-box;margin:0;padding:0}
html,body{width:1121px;height:1200px;overflow:hidden;background:var(--white)}
body{position:relative;font-family:"Bitter",Georgia,serif;color:var(--text)}
.abs{position:absolute}

/* header */
.site-header{left:0;top:0;width:1121px;height:98px;border-top:2px solid #9c9c9c;border-bottom:2px solid var(--maroon);background:#fbfbfb}
.brand{left:74px;top:9px;display:flex;align-items:center;gap:12px}
.brand-mark{width:72px;height:80px;border:3px solid var(--maroon)}
.brand-name{font-size:36px;color:var(--grey);font-weight:400}
.social{display:flex;gap:9px}
.social span{width:23px;height:23px;border-radius:50%;background:#2f6db0;display:block}
.social span:nth-child(2){background:#3fa6dc}
.social span:nth-child(3){background:#1f77b5}
.social span:nth-child(4){background:#d64531}
.header-social{left:564px;top:16px}
.call{left:788px;top:10px;display:flex;align-items:center;gap:6px;color:var(--maroon);font-size:18px}
.main-nav{left:564px;top:66px;display:flex;gap:24px;font-size:16px;color:var(--grey)}
.main-nav .active{color:var(--maroon)}

/* hero */
.hero{left:0;top:98px;width:1121px;height:411px;background:linear-gradient(#d2d1d6,#dedde1);border-bottom:3px solid var(--maroon)}
.hero-title{left:86px;top:120px;font-size:30px;line-height:36px;color:var(--maroon);font-weight:400}
.hero-photo{left:30px;top:200px;width:600px;height:306px;background:radial-gradient(ellipse at 55% 55%,#f1f1f3 0%,#bfc0c4 55%,#d4d3d8 80%);border-radius:40% 40% 6px 6px}
.slide-arrow{width:36px;height:36px;border-radius:50%;background:#6a6a6a;top:284px}
.dots{left:95px;top:484px;display:flex;gap:9px}
.dots span{width:17px;height:15px;background:#fff;display:block}
.dots .on{background:var(--maroon)}

/* booking */
.booking{left:654px;top:98px;width:395px;height:410px;background:var(--maroon);padding:0 5px 5px}
.tabs{display:flex;height:42px;align-items:flex-end;font-size:15px;color:#fff}
.tabs .tab-on{background:#8e8e8e;padding:8px 10px 7px;margin-top:6px}
.tabs .tab{padding:0 0 14px 12px}
.booking-body{background:#fff;height:364px;position:relative;font-size:13px}
.step{position:absolute;left:4px;width:22px;height:24px;border:1px solid var(--maroon);text-align:center;font-size:14px;line-height:22px}
.step-rule{position:absolute;left:26px;width:1px;background:var(--maroon)}
.field{position:absolute;height:26px;border:1px solid #999;font-size:12px;padding:5px 6px;font-family:"Open Sans",sans-serif}
.label{position:absolute;left:46px}
.link{position:absolute;left:46px;color:var(--maroon);text-decoration:underline}
.check{position:absolute;display:flex;align-items:center;gap:6px}
.check i{width:9px;height:9px;border:1px solid #666;display:block}
.help{width:20px;height:20px;border-radius:50%;background:#8a948d;color:#fff;font-size:10px;text-align:center;line-height:20px;display:inline-block}
.spin{position:absolute;right:0;top:0;width:20px;height:24px;border-left:1px solid #999;font-size:8px;text-align:center;line-height:11px}
.quote{position:absolute;left:255px;top:334px;width:128px;height:36px;background:var(--maroon);color:#fff;font-size:16px;text-align:center;line-height:36px}

/* features */
.features{left:0;top:511px;width:1121px;height:252px;background:var(--band);border-bottom:1px solid #e2e2e2}
.feature{position:absolute;top:30px;width:250px;text-align:center}
.feature-icon{width:88px;height:88px;border-radius:50%;border:2px solid #8a8a8a;margin:0 auto 20px;display:flex;align-items:center;justify-content:center;background:#fff}
.feature-icon.on{border-color:var(--maroon)}
.feature h3{font-size:15px;font-weight:400;line-height:20px;color:#333}
.feature p{font-family:"Open Sans",sans-serif;font-size:14px;line-height:19px;margin-top:8px;color:#444}
.side-box{top:617px;width:25px;height:38px;background:#c9c9c9}

/* content */
.section-title{left:0;width:1121px;text-align:center;font-size:18px;color:var(--grey)}
.section-title b{font-weight:400;color:var(--maroon)}
.dash{left:342px;width:437px;border-top:1px dashed #999}
.copy{left:0;width:1121px;text-align:center;font-size:13.5px;line-height:21px;color:#222}
.divider{left:80px;top:960px;width:961px;height:16px;background:radial-gradient(ellipse at 50% 0%,rgba(0,0,0,.14),rgba(0,0,0,0) 70%)}

/* footer */
.site-footer{left:0;top:1146px;width:1121px;height:54px;background:var(--maroon);color:#fff}
.foot-nav{left:76px;top:18px;display:flex;gap:18px;font-size:14px}
.foot-social{left:623px;top:15px}
.foot-social span{border:2px solid #fff}
.copyright{right:22px;top:19px;font-family:"Open Sans",sans-serif;font-size:13px;font-weight:600}
</style>
</head>
<body>

<header class="site-header abs">
  <div class="brand abs" style="left:74px;top:7px">
    <div class="brand-mark"></div>
    <div class="brand-name">Crestvane</div>
  </div>
  <div class="social header-social abs"><span></span><span></span><span></span><span></span></div>
  <div class="call abs">
    <svg width="38" height="40" viewBox="0 0 38 40" aria-hidden="true"><path d="M7 22 V17 a12 12 0 0 1 24 0 V22" fill="none" stroke="#555" stroke-width="3"/><rect x="4" y="19" width="7" height="12" rx="2" fill="var(--maroon)"/><rect x="27" y="19" width="7" height="12" rx="2" fill="var(--maroon)"/><path d="M30 31 q0 5 -8 6" fill="none" stroke="#555" stroke-width="2"/></svg>
    <span>Call us at +971 4 555 0182</span>
  </div>
  <nav class="main-nav abs"><span class="active">HOME</span><span>ABOUT US</span><span>OUR TEAM</span><span>STRATEGY</span><span>CONTACT US</span></nav>
</header>

<section class="hero abs"></section>
<h1 class="hero-title abs">Experience An Extra Mile of comfort,<br>pleasure and leisure From the best</h1>
<div class="hero-photo abs" role="img" aria-label="Photo of a silver saloon car on a light grey backdrop"></div>
<svg class="slide-arrow abs" style="left:22px" viewBox="0 0 36 36" aria-hidden="true"><circle cx="18" cy="18" r="18" fill="#5e5e5e"/><path d="M21 10 L13 18 L21 26" fill="none" stroke="#fff" stroke-width="2"/></svg>
<svg class="slide-arrow abs" style="left:1063px" viewBox="0 0 36 36" aria-hidden="true"><circle cx="18" cy="18" r="18" fill="#777"/><path d="M15 10 L23 18 L15 26" fill="none" stroke="#fff" stroke-width="2"/></svg>
<div class="dots abs"><span></span><span class="on"></span><span></span><span></span></div>

<form class="booking abs">
  <div class="tabs"><span class="tab-on">Book A Car</span><span class="tab">View / Modify / Cancel A Reservation</span></div>
  <div class="booking-body">
    <span class="step" style="top:10px">1</span>
    <span class="step-rule" style="top:34px;height:150px"></span>
    <span class="label" style="top:13px">Pick-up Location &nbsp;(City, State or Airport Code</span>
    <span class="link" style="top:35px">Previous Searches</span>
    <span class="field" style="left:46px;top:58px;width:318px">Dubai Airport - Terminal 3</span>
    <span class="link" style="top:91px">Help me find a rental location</span>
    <span class="check" style="left:46px;top:113px"><i></i>Return car to a different Crestvane Location <span class="help">?</span></span>
    <span class="step" style="top:148px">2</span>
    <span class="label" style="top:150px">Pick-up Date &amp; Time</span>
    <span class="field" style="left:46px;top:173px;width:158px">26/03/2015</span>
    <span class="field" style="left:208px;top:173px;width:156px">16:00<span class="spin">^<br>v</span></span>
    <span class="label" style="top:210px">Return Date &amp; Time</span>
    <span class="field" style="left:46px;top:233px;width:158px">26/03/2015</span>
    <span class="field" style="left:208px;top:233px;width:156px">16:00<span class="spin">^<br>v</span></span>
    <span class="label" style="top:270px">Hire Car Type</span>
    <span class="field" style="left:46px;top:293px;width:158px">Automatic</span>
    <span class="check" style="left:212px;top:295px;font-size:12px"><i></i>Apply a discount Code <span class="help">?</span></span>
    <span class="quote">Get A Quote</span>
  </div>
</form>

<section class="features abs">
  <div class="feature" style="left:63px">
    <div class="feature-icon on"><svg width="58" height="44" viewBox="0 0 58 44" aria-hidden="true"><path d="M4 26 l5 -10 h18 l5 10 v8 h-28z" fill="var(--maroon)"/><path d="M22 34 l5 -10 h20 l5 10 v8 h-30z" fill="var(--maroon)" stroke="#fff" stroke-width="2"/></svg></div>
    <h3>Wide Range Of Vehicles For City<br>Driving or SUV's For Trips</h3>
    <p>Lorem ipsum dolor sit<br>aonsectetuer adipiscing elied<br>diam nonummy</p>
  </div>
  <div class="feature" style="left:327px">
    <div class="feature-icon"><svg width="40" height="40" viewBox="0 0 40 40" aria-hidden="true"><path d="M6 22 L20 6 H34 V20 L18 34 Z" fill="#777"/><circle cx="28" cy="12" r="2.5" fill="#fff"/><path d="M14 24 L24 16" stroke="#fff" stroke-width="2"/></svg></div>
    <h3>Special 10% Discount For New<br>Customers On The First Rent</h3>
    <p>Lorem ipsum dolor sit<br>aonsectetuer adipiscing elied<br>diam nonummy</p>
  </div>
  <div class="feature" style="left:576px">
    <div class="feature-icon"><svg width="44" height="44" viewBox="0 0 44 44" aria-hidden="true"><circle cx="14" cy="10" r="5" fill="#666"/><rect x="18" y="8" width="16" height="4" fill="#666"/><path d="M8 32 l5 -10 h18 l5 10 v8 h-28z" fill="#666"/></svg></div>
    <h3>Long Term Car<br>Rentals</h3>
    <p>Lorem ipsum dolor sit<br>aonsectetuer adipiscing elied<br>diam nonummy</p>
  </div>
  <div class="feature" style="left:826px">
    <div class="feature-icon"><svg width="40" height="40" viewBox="0 0 40 40" aria-hidden="true"><path d="M16 8 L6 18 L16 28 V22 q14 -2 14 12 q6 -20 -14 -22z" fill="#666"/></svg></div>
    <h3>Buyback Option After<br>Lease Term</h3>
    <p>Lorem ipsum dolor sit<br>aonsectetuer adipiscing elied<br>diam nonummy</p>
  </div>
</section>
<svg class="side-box abs" style="left:32px" viewBox="0 0 25 38" aria-hidden="true"><rect width="25" height="38" fill="#c9c9c9"/><path d="M16 10 L9 19 L16 28" fill="none" stroke="#fff" stroke-width="2"/></svg>
<svg class="side-box abs" style="left:1064px" viewBox="0 0 25 38" aria-hidden="true"><rect width="25" height="38" fill="#c9c9c9"/><path d="M9 10 L16 19 L9 28" fill="none" stroke="#fff" stroke-width="2"/></svg>

<h2 class="section-title abs" style="top:792px;font-weight:400">Welcome to Crestvane <b>Rent A Car</b></h2>
<div class="dash abs" style="top:820px"></div>
<p class="copy abs" style="top:826px">As Dubai is expected to welcome millions of tourists and visitors, car rental industry is believed to escalate more rapidly in the region.<br>Over the past five years, demands for car rentals in Dubai has been augmenting at a healthy pace and is currently registering a growth<br>rate of 20 to 25 percent per year. The swift economic growth and the number. Crestvane was established to bring comfort<br>and pleasure to all its clients. First rate service plus highly maintained and top...</p>
<p class="copy abs" style="top:914px;font-size:14px">Read More</p>
<div class="divider abs"></div>

<h2 class="section-title abs" style="top:1000px;font-weight:400">Our <b>Mission</b></h2>
<div class="dash abs" style="top:1028px"></div>
<p class="copy abs" style="top:1042px">To be one of the leading auto leasing company in the fast growing economy and tourism industry of the emirate of Dubai &amp; &nbsp;play alongside<br>with the major car rental companies in the globe.</p>
<p class="copy abs" style="top:1088px">Crestvane vows to deliver comfort, luxury &amp; satisfaction to all our clients by providing them professional, hassle-free and first class service.</p>

<footer class="site-footer abs">
  <nav class="foot-nav abs"><span>HOME</span><span>ABOUT US</span><span>OUR TEAM</span><span>STRATEGY</span><span>CONTACT US</span></nav>
  <div class="social foot-social abs"><span></span><span></span><span></span><span></span></div>
  <div class="copyright abs">© 2015 Crestvane. All Rights Reserved</div>
</footer>

</body>
</html>
```